VFX Company Business Card Design Project

The Kestrel Works is a decentralized Visual Effects Studio servicing the television and feature film industries.
Project Brief:
Take our logo that was previously designed on Pencil Harbor and make a double sided business card.
Requirements:
- Card MUST be double sided.
- Front of card MUST have the yellow part of our logo against the dark grey background.
- Back of card is completely up to the designer.
- Back of card must include the complete company logo.
Please follow these File Preparation guidelines:
http://printnook.ca/infopage?file=filetype_en&s=PrintNook_new&lang=en
Business

```html
<!DOCTYPE html>
<html lang="en">
<head>
<meta charset="utf-8">
<title>The Kestrel Works – Business Card</title>
<link rel="stylesheet" href="https://fonts.googleapis.com/css2?family=Questrial&family=Source+Sans+3:wght@400;600&display=swap">
<style>
  :root {
    --backdrop: #d9b48e;
    --card-dark: #2a2a2a;
    --swoosh-grey: #5f6e73;
    --logo-yellow: #f9c623;
    --text-light: #f2f2f2;
    --text-muted: #d6d6d6;
    --label-ink: #1c1c1c;
  }
  * { box-sizing: border-box; margin: 0; padding: 0; }
  html, body { width: 1200px; height: 788px; overflow: hidden; }
  body {
    position: relative;
    background: var(--backdrop);
    font-family: "Questrial", "Century Gothic", sans-serif;
    color: var(--text-light);
  }
  .side-label {
    position: absolute;
    font-family: "Source Sans 3", "Myriad Pro", sans-serif;
    font-size: 22px;
    color: var(--label-ink);
    transform: translateX(-50%);
  }
  .label-back { left: 600px; top: 32px; }
  .label-front-1 { left: 327px; top: 403px; }
  .label-front-2 { left: 900px; top: 403px; }

  .card {
    position: absolute;
    width: 524px;
    height: 299px;
    border-radius: 22px;
    background: var(--card-dark);
    overflow: hidden;
    box-shadow: 3px 4px 10px rgba(0,0,0,0.35);
  }
  .card-back { left: 338px; top: 78px; }
  .card-front-1 { left: 54px; top: 446px; }
  .card-front-2 { left: 622px; top: 446px; }

  .swoosh { position: absolute; inset: 0; width: 100%; height: 100%; }

  .brand-name {
    position: absolute;
    white-space: nowrap;
    font-family: "Questrial", "Century Gothic", sans-serif;
  }
  .card-back .brand-name {
    left: 22px; top: 52px;
    font-size: 34px;
    color: var(--text-muted);
  }

  .holder {
    position: absolute;
    left: 24px; top: 163px;
    font-size: 20px;
    letter-spacing: 0.5px;
  }
  .holder .designation { font-size: 14px; letter-spacing: 0.6px; }

  .contact-list {
    position: absolute;
    left: 22px; top: 203px;
    list-style: none;
    font-size: 14px;
    line-height: 22px;
  }
  .contact-list b { font-style: italic; font-weight: 700; display: inline-block; width: 20px; }
  .address {
    position: absolute;
    left: 189px; top: 250px;
    padding-left: 7px;
    border-left: 1px solid #6a6a6a;
    font-size: 13px;
    line-height: 18px;
  }

  .card-front-1 .brand-name {
    left: 50%; top: 118px;
    transform: translateX(-50%);
    font-size: 48px;
    color: var(--logo-yellow);
  }
  .front-2-lockup {
    position: absolute;
    left: 50%; top: 124px;
    transform: translateX(-50%);
    display: flex; align-items: center; gap: 18px;
  }
  .brand-dot {
    width: 48px; height: 48px; border-radius: 50%;
    background: var(--logo-yellow);
  }
  .card-front-2 .brand-name {
    position: static;
    font-size: 40px;
    color: var(--text-muted);
  }
  .website {
    position: absolute;
    left: 0; right: 0; top: 256px;
    text-align: center;
    font-size: 20px;
    letter-spacing: 3px;
  }
</style>
</head>
<body>
  <div class="side-label label-back">Back</div>
  <div class="side-label label-front-1">Front - 1</div>
  <div class="side-label label-front-2">Front - 2</div>

  <section class="card card-back">
    <svg class="swoosh" viewBox="0 0 524 299" preserveAspectRatio="none" aria-hidden="true">
      <path d="M362,0 C470,60 505,200 442,299 L524,299 L524,0 Z" fill="var(--swoosh-grey)"/>
      <path d="M425,0 C492,55 505,165 488,262 C494,160 472,62 446,0 Z" fill="var(--card-dark)"/>
    </svg>
    <div class="brand-name">The Kestrel Works</div>
    <div class="holder">Your Name, <span class="designation">Designation</span></div>
    <ul class="contact-list">
      <li><b>c :</b> 123-456-7890</li>
      <li><b>p :</b> 123-456-7890</li>
      <li><b>e :</b> info@website.com</li>
      <li><b>w :</b> www.website.com</li>
    </ul>
    <div class="address">0000#, Area Name<br>State Name, Country code</div>
  </section>

  <section class="card card-front-1">
    <div class="brand-name">The Kestrel Works</div>
    <div class="website">www.website.com</div>
  </section>

  <section class="card card-front-2">
    <div class="front-2-lockup">
      <span class="brand-dot"></span>
      <span class="brand-name">The Kestrel Works</span>
    </div>
    <div class="website">www.website.com</div>
  </section>
</body>
</html>
```